Road Construction Company needs business cards

We would like a new business card designed for our business.

We're a road construction company based in Qld, Australia.

Can the business card please have the following information on it.

Name: Warren Halbeck
Position: General Manager
Phone: 0472 915 348
Email: Warren.halbeck@tovrin.com.au
Address: 87 Marrow Ave, Pendlebay, QLD, 4023
Website: www.tovrin.com.au

Visually we'd like the card to be professional and simple.

Attached is our logo.

Our website is www.tovrin.com.au

Target Market(s)

Men aged 25-60

Contact Information for Business Card

As listed in project description

Font styles to use
Serif

Requirements
Must have
• Large logo on back of card

```html
<!DOCTYPE html>
<html lang="en">
<head>
<meta charset="utf-8">
<title>Tovrin Business Card</title>
<link rel="stylesheet" href="https://fonts.googleapis.com/css2?family=Open+Sans:wght@700&display=swap">
<style>
  :root {
    --backdrop: #5f5f5f;
    --brand-blue: #0b52a0;
    --ink-blue: #1b4f94;
    --paper: #ffffff;
  }
  * { margin: 0; padding: 0; box-sizing: border-box; }
  html, body {
    width: 1200px;
    height: 1194px;
    overflow: hidden;
    background: var(--backdrop);
    font-family: "Open Sans", Arial, sans-serif;
    font-weight: 700;
  }
  .sheet {
    position: relative;
    width: 1200px;
    height: 1194px;
  }
  .card {
    position: absolute;
    top: 29px;
    width: 564px;
    height: 322px;
  }
  .card--back {
    left: 29px;
    background: var(--brand-blue);
    display: flex;
    align-items: center;
    justify-content: center;
  }
  .wordmark {
    color: var(--paper);
    font-size: 44px;
    letter-spacing: 1px;
    line-height: 1;
    margin-top: -10px;
  }
  .card--front {
    left: 607px;
    background: var(--paper);
    color: var(--ink-blue);
  }
  .identity {
    position: absolute;
    top: 47px;
    right: 55px;
    text-align: right;
  }
  .identity__name {
    font-size: 14px;
    line-height: 18px;
    letter-spacing: 0.2px;
  }
  .identity__role {
    font-size: 8.5px;
    line-height: 14px;
    margin-right: 14px;
  }
  .contacts {
    position: absolute;
    left: 44px;
    top: 172px;
    list-style: none;
  }
  .contacts__item {
    display: flex;
    align-items: center;
    height: 31.5px;
    font-size: 12.5px;
    letter-spacing: 0.3px;
  }
  .contacts__icon {
    width: 12px;
    height: 12px;
    margin-right: 7px;
    flex: none;
  }
</style>
</head>
<body>
<main class="sheet">
  <section class="card card--back" aria-label="Card back">
    <div class="wordmark">TOVRIN</div>
  </section>

  <section class="card card--front" aria-label="Card front">
    <div class="identity">
      <p class="identity__name">Name: Warren Halbeck</p>
      <p class="identity__role">Position: General Manager</p>
    </div>

    <ul class="contacts">
      <li class="contacts__item">
        <svg class="contacts__icon" viewBox="0 0 12 12" aria-hidden="true">
          <circle cx="6" cy="6" r="6" fill="var(--ink-blue)"/>
          <path d="M4 3.2 L5.1 3 L5.6 4.6 L4.9 5.1 Q5.5 6.5 6.9 7.1 L7.4 6.4 L9 6.9 L8.8 8 Q6.6 8.5 4.8 6.9 Q3.4 5.3 4 3.2Z" fill="#fff"/>
        </svg>
        Phone: 0472 915 348
      </li>
      <li class="contacts__item">
        <svg class="contacts__icon" viewBox="0 0 12 12" aria-hidden="true">
          <circle cx="6" cy="6" r="6" fill="var(--ink-blue)"/>
          <rect x="3" y="4" width="6" height="4.2" fill="#fff"/>
          <path d="M3 4 L6 6.3 L9 4" fill="none" stroke="var(--ink-blue)" stroke-width="0.7"/>
        </svg>
        Email: Warren.halbeck@tovrin.com.au
      </li>
      <li class="contacts__item">
        <svg class="contacts__icon" viewBox="0 0 12 12" aria-hidden="true">
          <circle cx="6" cy="6" r="6" fill="var(--ink-blue)"/>
          <path d="M6 2.8 L9.2 5.8 H8.2 V8.8 H6.8 V7 H5.2 V8.8 H3.8 V5.8 H2.8Z" fill="#fff"/>
        </svg>
        Address: 87 Marrow Ave, Pendlebay, QLD, 4023
      </li>
      <li class="contacts__item">
        <svg class="contacts__icon" viewBox="0 0 12 12" aria-hidden="true">
          <circle cx="6" cy="6" r="6" fill="var(--ink-blue)"/>
          <circle cx="6" cy="6" r="3" fill="none" stroke="#fff" stroke-width="0.9"/>
          <path d="M3 6 H9 M6 3 Q4.6 6 6 9 M6 3 Q7.4 6 6 9" fill="none" stroke="#fff" stroke-width="0.7"/>
        </svg>
        Website: www.tovrin.com.au
      </li>
    </ul>
  </section>
</main>
</body>
</html>
```